FinTech company looking to revamp and expand client-facing interface for our financial models

Pellworth Engines currently has a very simple website that allows clients to interact with our financial models. We are looking to completely redesign the current site and add several extra pages to provide extra functionality. We want the design to have a modern, slick feel, that will work on both a desktop or a tablet. It should be straightforward for clients to move between different pages at any time, and clear from the layout how to interact with the more advanced features. We have included screenshots of existing pages in the attached design brief, as well as sketches of the functionality required by the new pages, but can't provide a direct link to the current site.
Target Market(s)
Professional investors that will be paying to access the interface
Industry/Entity Type
Finance
Number of Pages Required
4 page
Colors
Designer to choose colors to be used in the design.
Look and feel
Each slider illustrates characteristics of the customer's brand and the style your logo design should communicate.

```html
<!DOCTYPE html>
<html lang="en">
<head>
<meta charset="utf-8">
<title>Pellworth Models Dashboard</title>
<link href="https://fonts.googleapis.com/css2?family=Mulish:wght@400;600;700&family=Roboto+Slab:wght@400&family=Roboto+Condensed:wght@400;700&display=swap" rel="stylesheet">
<style>
  :root{
    --page:#eefdd6;
    --surface:#f7f7f7;
    --bar:#242424;
    --tab-active:#121212;
    --accent:#9dbf65;
    --row-alt:#fefde8;
    --line:#d9d9d9;
    --text:#3a3a3a;
    --muted:#666;
    --nav-text:#bdbdbd;
  }
  *{box-sizing:border-box;margin:0;padding:0}
  html,body{width:828px;height:1200px;overflow:hidden;background:var(--page)}
  body{position:relative;font-family:"Mulish",sans-serif;color:var(--text)}
  .screen{position:absolute;left:52px;width:724px;height:549px;background:var(--surface);box-shadow:0 1px 3px rgba(0,0,0,.12)}
  .screen--models{top:36px}
  .screen--factors{top:613px}
  .topbar{position:absolute;left:0;top:0;width:100%;height:60px;background:var(--bar)}
  .brand{position:absolute;left:10px;top:15px;font-family:"Roboto Slab",serif;font-size:21px;color:#fff;letter-spacing:.2px}
  .tabs{position:absolute;top:0;height:60px;display:flex}
  .tab{width:44.5px;height:60px;line-height:60px;text-align:center;font-size:9px;color:#ccc;font-family:"Mulish",sans-serif}
  .tab--active{background:var(--tab-active);color:#ddd}
  .screen--models .tabs{left:124.5px}
  .screen--factors .tabs{left:121.5px}
  .menu{position:absolute;right:12px;top:0;height:60px;display:flex;align-items:center;gap:19px;font-family:"Roboto Condensed",sans-serif;font-size:7.6px;color:var(--nav-text);letter-spacing:.1px}
  .menu-item{display:flex;align-items:center;gap:3px}
  .menu-item svg{width:9px;height:9px;fill:var(--nav-text)}
  .filters{position:absolute;left:11px;top:78px}
  .filter{position:relative;height:24px;margin-bottom:9.5px;width:270px}
  .filter-name{position:absolute;left:0;top:5px;font-size:10px;color:var(--muted)}
  .filter-label{position:absolute;top:5px;font-size:10px;font-weight:700;color:#222}
  .screen--models .filter-label{left:51px}
  .screen--factors .filter-label{left:46px}
  .filter-input{position:absolute;left:109px;top:0;width:146px;height:24px;background:#fff;border:1px solid #ccc;border-radius:2px;font-size:8px;padding:8px 0 0 5px;color:#333}
  .export{position:absolute;left:11px;display:flex;align-items:center;gap:4px;font-size:10.5px;color:var(--accent)}
  .export svg{width:11px;height:11px}
  .screen--models .export{top:154px}
  .screen--factors .export{top:191px}
  table{position:absolute;left:11px;border-collapse:collapse;table-layout:fixed;font-size:8.6px}
  .screen--models table{top:180.5px;width:701px}
  .screen--factors table{top:218px;width:612px}
  th{background:var(--accent);color:#fff;font-weight:600;height:43.6px;text-transform:uppercase;font-size:8.6px;letter-spacing:.2px;border-right:1px solid #b3cf85}
  td{height:44px;text-align:center;border:1px solid var(--line);color:var(--text);line-height:1.5}
  tbody tr:nth-child(even) td{background:var(--row-alt)}
  tbody tr:nth-child(odd) td{background:#fff}
  td.id{text-align:left;padding-left:4px}
  td.time{color:var(--accent)}
  .screen--factors td.sector{text-align:left;padding-left:14px}
  .screen--factors th.sector{text-align:left;padding-left:20px}
  .caret{display:inline-block;width:0;height:0;border-left:3px solid transparent;border-right:3px solid transparent;border-top:3.5px solid #fff;margin-left:4px;vertical-align:middle}
  .footer{position:absolute;left:0;bottom:0;width:100%;height:39.5px;background:var(--bar);color:#eee;font-family:Arial,sans-serif;font-size:7.8px}
  .footer-note{position:absolute;left:0;width:100%;top:15px;text-align:center}
  .footer-code{position:absolute;right:17px;top:25px}
</style>
</head>
<body>

<section class="screen screen--models">
  <header class="topbar">
    <div class="brand">Pellworth</div>
    <nav class="tabs"><span class="tab tab--active">250D</span><span class="tab">83D</span><span class="tab">42D</span></nav>
    <nav class="menu">
      <span class="menu-item"><svg viewBox="0 0 10 10"><path d="M5 1 0.5 5h1.5v4h2.3V6.5h1.4V9H8V5h1.5z"/></svg>MODELS</span>
      <span class="menu-item"><svg viewBox="0 0 10 10"><path d="M5 0.5l1 1.3 1.6-.4.3 1.6 1.6.6-.7 1.5.7 1.5-1.6.6-.3 1.6-1.6-.4L5 9.5 4 8.2l-1.6.4-.3-1.6-1.6-.6.7-1.5-.7-1.5 1.6-.6.3-1.6 1.6.4z" fill="none" stroke="#bdbdbd" stroke-width="0.9"/><circle cx="5" cy="5" r="1.6" fill="none" stroke="#bdbdbd" stroke-width="0.9"/></svg>SENSITIVITES</span>
      <span class="menu-item"><svg viewBox="0 0 10 10"><path d="M5 0.5l1.4 3 3.1.3-2.4 2.1.7 3.1L5 7.4 2.2 9l.7-3.1L.5 3.8l3.1-.3z"/></svg>FAVOURITES</span>
    </nav>
  </header>

  <div class="filters">
    <div class="filter"><span class="filter-name">Quality</span><span class="filter-label">Threshold :</span><div class="filter-input">-10</div></div>
    <div class="filter"><span class="filter-name">Abs\.stat</span><span class="filter-label">Threshold :</span><div class="filter-input">-10</div></div>
  </div>

  <div class="export"><svg viewBox="0 0 12 12" fill="none" stroke="#9dbf65" stroke-width="1.3"><path d="M9 7v3.5H1.5V3H5"/><path d="M7 1h4v4M11 1 5.5 6.5"/></svg>Export</div>

  <table>
    <colgroup><col style="width:41.5px"><col style="width:81px"><col style="width:105px"><col style="width:73px"><col style="width:49px"><col style="width:50px"><col style="width:50px"><col style="width:50px"><col style="width:50px"><col style="width:50px"><col style="width:50px"><col style="width:51.5px"></colgroup>
    <thead><tr><th>ID<span class="caret"></span></th><th>Sector</th><th>Time</th><th>Quality</th><th>Star 1</th><th>Star 2</th><th>Star 3</th><th>Star 4</th><th>Star 5</th><th>Star 6</th><th>Star 7</th><th>Star 8</th></tr></thead>
    <tbody>
      <tr><td class="id">Model 1</td><td>Materials</td><td class="time">2019-07-03<br>12:15:00.000</td><td>30.2288</td><td>2.01574</td><td>23.305</td><td>-0.149368</td><td>22.3054</td><td>4.63714</td><td>0.945706</td><td>2.81949</td><td>2.60858</td></tr>
      <tr><td class="id">Model 2</td><td>Industrials</td><td class="time">2019-07-03<br>12:15:00.000</td><td>30.2288</td><td>2.01574</td><td>23.305</td><td>-0.149368</td><td>22.3054</td><td>4.63714</td><td>0.945706</td><td>2.81949</td><td>2.60858</td></tr>
      <tr><td class="id">Model 3</td><td>Consumer<br>Discretionary</td><td class="time">2019-07-03<br>12:15:00.000</td><td>30.2288</td><td>2.01574</td><td>23.305</td><td>-0.149368</td><td>22.3054</td><td>4.63714</td><td>0.945706</td><td>2.81949</td><td>2.60858</td></tr>
      <tr><td class="id">Model 4</td><td>Information<br>Technology</td><td class="time">2019-07-03<br>12:15:00.000</td><td>30.2288</td><td>2.01574</td><td>23.305</td><td>-0.149368</td><td>22.3054</td><td>4.63714</td><td>0.945706</td><td>2.81949</td><td>2.60858</td></tr>
      <tr><td class="id">Model 5</td><td>Information<br>Technology</td><td class="time">2019-07-03<br>12:15:00.000</td><td>30.2288</td><td>2.01574</td><td>23.305</td><td>-0.149368</td><td>22.3054</td><td>4.63714</td><td>0.945706</td><td>2.81949</td><td>2.60858</td></tr>
    </tbody>
  </table>

  <footer class="footer"><div class="footer-note">© Copyright-2019 Pellworth.All rights reserved</div><div class="footer-code">C2</div></footer>
</section>

<section class="screen screen--factors">
  <header class="topbar">
    <div class="brand">Pellworth</div>
    <nav class="tabs"><span class="tab tab--active">250D</span><span class="tab">83D</span><span class="tab">42D</span></nav>
    <nav class="menu">
      <span class="menu-item"><svg viewBox="0 0 10 10"><path d="M5 1 0.5 5h1.5v4h2.3V6.5h1.4V9H8V5h1.5z"/></svg>MODELS</span>
      <span class="menu-item"><svg viewBox="0 0 10 10"><path d="M5 0.5l1 1.3 1.6-.4.3 1.6 1.6.6-.7 1.5.7 1.5-1.6.6-.3 1.6-1.6-.4L5 9.5 4 8.2l-1.6.4-.3-1.6-1.6-.6.7-1.5-.7-1.5 1.6-.6.3-1.6 1.6.4z" fill="none" stroke="#bdbdbd" stroke-width="0.9"/><circle cx="5" cy="5" r="1.6" fill="none" stroke="#bdbdbd" stroke-width="0.9"/></svg>SENSITIVITES</span>
      <span class="menu-item"><svg viewBox="0 0 10 10"><path d="M5 0.5l1.4 3 3.1.3-2.4 2.1.7 3.1L5 7.4 2.2 9l.7-3.1L.5 3.8l3.1-.3z"/></svg>FAVOURITES</span>
    </nav>
  </header>

  <div class="filters">
    <div class="filter"><span class="filter-name">Star 1</span><span class="filter-label">Threshold :</span><div class="filter-input">-10</div></div>
    <div class="filter"><span class="filter-name">Star 2</span><span class="filter-label">Threshold :</span><div class="filter-input">-10</div></div>
    <div class="filter"><span class="filter-name">Star 3</span><span class="filter-label">Threshold :</span><div class="filter-input">-10</div></div>
  </div>

  <div class="export"><svg viewBox="0 0 12 12" fill="none" stroke="#9dbf65" stroke-width="1.3"><path d="M9 7v3.5H1.5V3H5"/><path d="M7 1h4v4M11 1 5.5 6.5"/></svg>Export</div>

  <table>
    <colgroup><col style="width:70.5px"><col style="width:68.5px"><col style="width:173px"><col style="width:50px"><col style="width:50px"><col style="width:50px"><col style="width:50px"><col style="width:50px"><col style="width:50px"></colgroup>
    <thead><tr><th>Factor</th><th>ID<span class="caret"></span></th><th class="sector">Sector</th><th>Star 1</th><th>Star 2</th><th>Star 3</th><th>Star 4</th><th>Star 5</th><th>Star 6</th></tr></thead>
    <tbody>
      <tr><td>Factor 1</td><td>Model 1</td><td class="sector">Materials</td><td>2.01574</td><td>23.305</td><td>-0.149368</td><td>22.3054</td><td>4.63714</td><td>0.945706</td></tr>
      <tr><td>Factor 2</td><td>Model 2</td><td class="sector">Materials</td><td>2.01574</td><td>23.305</td><td>-0.149368</td><td>22.3054</td><td>4.63714</td><td>0.945706</td></tr>
      <tr><td>Factor 3</td><td>Model 3</td><td class="sector">Materials</td><td>2.01574</td><td>23.305</td><td>-0.149368</td><td>22.3054</td><td>4.63714</td><td>0.945706</td></tr>
      <tr><td>Factor 4</td><td>Model 4</td><td class="sector">Industrials</td><td>2.01574</td><td>23.305</td><td>-0.149368</td><td>22.3054</td><td>4.63714</td><td>0.945706</td></tr>
      <tr><td>Factor 5</td><td>Model 5</td><td class="sector">Industrials</td><td>2.01574</td><td>23.305</td><td>-0.149368</td><td>22.3054</td><td>4.63714</td><td>0.945706</td></tr>
    </tbody>
  </table>

  <footer class="footer"><div class="footer-note">© Copyright-2019 Pellworth.All rights reserved</div><div class="footer-code">C2</div></footer>
</section>

</body>
</html>
```